Popup Nightclub Grand Opening Flyer

We need to design a flyer for the grand opening of an upscale, exclusive nightclub called "Lantern". The design needs to be chic and exclusive. The background should be black and the text should primarily be white. We like minimalist designs.

Here is the text for the flyer
-
Velvetroll Atlanta Presents

Lantern (LOGO)

A Popup Nightclub Experience
For one night Only

Friday, October 18, 2013
Party begins at 9PM

INVITE ONLY

See invitation for location details
(Velvetroll Atlanta logo)

-
Examples we like

http://cdn4-x.pressfolio-example.com/sites/default/files/styles/image_content_width/hash/3b/fd/2468013579_4421_flyer.jpg?itok=K9rtQw2z

http://files.hubspace-example.net/files/8Hqq-Tr72WWE3kaRbTmcxP5QZK2F396J8nbRw4CKMHfdX2Y7qSEF-MqjxDoNrLY3QCyQJD7npjGaRq3k-Mhx6hqf3MDSWf8r3/2zenSaturdays.jpg

http://morvex-example.com/wp-content/uploads/siteskin/widgetkit/gallery/2zen/2zen-gen_qstay4-01.jpg

Hi All, one thing that we are seeing that we don't like is on over emphasis on the phrase "a popup nightclub experience" please don't make this the largest thing on the flyer

Target Market(s)

Target market is 25-35 year olds who are affluent (rich) and like luxury brands

Requirements
Must have
• Dark Background
Nice to have
• Velvetroll Logo on the bottom
Modern text that isn't curvy
Should not have
• Curved text

```html
<!DOCTYPE html>
<html lang="en">
<head>
<meta charset="utf-8">
<title>Lantern Nightclub – Velvetroll Atlanta Presents</title>
<link rel="stylesheet" href="https://fonts.googleapis.com/css2?family=Open+Sans:wght@400&family=Montserrat:wght@200;300&family=Arimo:wght@700&family=Libre+Baskerville:wght@700&display=swap">
<style>
  :root {
    --ink-black: #0b0b0b;
    --weave-dark: #060606;
    --weave-light: #1c1c1c;
    --text-white: #ffffff;
    --logo-silver: #d9d9d9;
    --band-yellow: #f6ec3f;
  }
  * { margin: 0; padding: 0; box-sizing: border-box; }
  html, body {
    width: 851px; height: 1200px; overflow: hidden;
    background: var(--ink-black);
  }
  .flyer {
    position: relative; width: 851px; height: 1200px; overflow: hidden;
    color: var(--text-white);
    font-family: "Open Sans", Arial, sans-serif;
  }
  .weave-texture {
    position: absolute; inset: 0;
    background: radial-gradient(ellipse at 50% 45%, var(--weave-light) 0%, #111 55%, var(--weave-dark) 100%);
  }
  .presenter {
    position: absolute; top: 80px; left: 0; width: 100%;
    text-align: center; font-size: 27px; font-weight: 400;
  }
  .accent-band {
    position: absolute; left: 112px; width: 622px; height: 54px;
    background: var(--band-yellow);
  }
  .accent-band--top { top: 130px; }
  .accent-band--bottom { top: 524px; }
  .venue-mark {
    position: absolute; top: 222px; left: 0; width: 100%;
    display: flex; flex-direction: column; align-items: center;
  }
  .venue-dot {
    width: 110px; height: 110px; border-radius: 50%;
    background: var(--logo-silver);
  }
  .venue-name {
    margin-top: 78px;
    font-family: "Montserrat", Arial, sans-serif; font-weight: 200;
    font-size: 62px; letter-spacing: 10px; line-height: 1;
    color: var(--text-white);
  }
  .tagline {
    position: absolute; left: 140px;
    font-family: "Arimo", Arial, sans-serif; font-weight: 700;
    font-variant: small-caps; font-size: 22px; letter-spacing: 4.4px;
  }
  .tagline--first { top: 602px; }
  .tagline--second { top: 646px; }
  .event-date, .event-time {
    position: absolute; left: 0; width: 100%; text-align: center;
    font-family: "Arimo", Arial, sans-serif; font-weight: 700;
    font-size: 20px; letter-spacing: 4px; padding-left: 30px;
  }
  .event-date { top: 727px; }
  .event-time { top: 767px; }
  .invite-only {
    position: absolute; top: 847px; left: 0; width: 100%; text-align: center;
    font-family: "Libre Baskerville", Georgia, serif; font-weight: 700;
    font-size: 20px; padding-left: 14px;
  }
  .location-note {
    position: absolute; top: 911px; left: 0; width: 100%; text-align: center;
    font-family: "Arimo", Arial, sans-serif; font-weight: 700;
    font-size: 16px; padding-left: 10px;
  }
  .host-mark {
    position: absolute; top: 990px; left: 0; width: 100%;
    display: flex; justify-content: center; align-items: center; gap: 24px;
  }
  .host-dot {
    width: 58px; height: 58px; border-radius: 50%;
    background: var(--text-white);
  }
  .host-name {
    font-family: "Montserrat", Arial, sans-serif; font-weight: 300;
    font-size: 38px; letter-spacing: 6px; color: var(--text-white);
  }
</style>
</head>
<body>
  <main class="flyer">
    <div class="weave-texture" role="img" aria-label="Black carbon fibre weave texture background"></div>

    <p class="presenter">Velvetroll Atlanta Presents</p>

    <div class="accent-band accent-band--top"></div>

    <div class="venue-mark">
      <div class="venue-dot"></div>
      <h1 class="venue-name">LANTERN</h1>
    </div>

    <div class="accent-band accent-band--bottom"></div>

    <p class="tagline tagline--first">A Popup Nightclub Experience</p>
    <p class="tagline tagline--second">For one night Only</p>

    <p class="event-date">FRIDAY, OCTOBER&nbsp; 18, 2013</p>
    <p class="event-time">PARTY BEGINS AT 9PM</p>

    <p class="invite-only">Invite Only</p>
    <p class="location-note">See invitation for location details</p>

    <div class="host-mark">
      <div class="host-dot"></div>
      <span class="host-name">VELVETROLL ATLANTA</span>
    </div>
  </main>
</body>
</html>
```